Stylish Business Cards Wanted

- DOUBLE SIDED Design Required -

High end, edgy cards for a corporate and personal stylist. Must include logo,
Name: Belinda Harwick
Title: Director and Stylist
telephone : +61 8 7142 5809
email: belinda@theloombriefing.example
website: theloombriefing.example
Tag: Corporate Workwear & Uniform Specialist | Personal Stylist
Would like nice icons for telephone, email, website

Target Market(s)

Businesses wanting stylish uniforms, people wanting stylish wardrobes

Industry/Entity Type

Corporate Workwear Stylist

Contact Information for Business Card

I would like black, white and gold foiling incorporated in the design - possibly a touch of the other colours on my branding guide attached Name: Belinda Harwick Title: Director and Stylist telephone : +61 8 7142 5809 email: belinda@theloombriefing.example website: theloombriefing.example Tag: Corporate Workwear & Uniform Specialist | Personal Stylist Would like nice icons for telephone, email, website

Font styles to use
Other font styles liked:
• Raleway

Colors

Designer to choose colors to be used in the design.

Requirements
Must have
• Gold foil accents

```html
<!DOCTYPE html>
<html lang="en">
<head>
<meta charset="utf-8">
<title>The Loom Briefing – Business Cards</title>
<link rel="stylesheet" href="https://fonts.googleapis.com/css2?family=Montserrat:wght@400;600;700&family=Raleway:wght@400;500&display=swap">
<style>
  :root {
    --backdrop: #bdbdbd;
    --card: #242424;
    --gold: #e8bf5a;
    --white: #ffffff;
    --ink: #1e1e1e;
  }
  * { box-sizing: border-box; margin: 0; padding: 0; }
  html, body { width: 1200px; height: 788px; overflow: hidden; }
  body {
    background: var(--backdrop);
    display: flex;
    align-items: center;
    justify-content: center;
    gap: 44px;
    font-family: "Raleway", Arial, sans-serif;
  }
  .card {
    background: var(--card);
    position: relative;
    box-shadow: 0 10px 30px rgba(0,0,0,0.25);
  }

  /* Brand name */
  .brand {
    display: flex;
    align-items: center;
    gap: 12px;
    font-family: "Montserrat", Arial, sans-serif;
    font-weight: 700;
    color: var(--white);
    letter-spacing: 0.02em;
    line-height: 1;
  }
  .brand-mark {
    width: 14px; height: 14px;
    background: var(--gold);
    flex: none;
  }

  /* Portrait card (contact side) */
  .card-contact {
    width: 340px;
    height: 595px;
    display: flex;
    flex-direction: column;
    align-items: center;
  }
  .card-contact .brand {
    margin-top: 140px;
    font-size: 28px;
  }
  .name-band {
    position: absolute;
    left: 0; right: 0;
    top: 300px;
    height: 96px;
    background: var(--gold);
    display: flex;
    flex-direction: column;
    align-items: center;
    justify-content: center;
    color: var(--ink);
  }
  .person-name {
    font-family: "Montserrat", Arial, sans-serif;
    font-weight: 700;
    font-size: 25px;
    letter-spacing: 0.01em;
    text-transform: uppercase;
  }
  .person-title {
    font-family: Arial, Helvetica, sans-serif;
    font-size: 17px;
    margin-top: 3px;
  }
  .icon-row {
    position: absolute;
    top: 426px;
    left: 28px; right: 28px;
    display: flex;
    align-items: center;
    gap: 8px;
  }
  .icon-row .rule {
    flex: 1;
    height: 1px;
    background: var(--gold);
  }
  .icon {
    width: 30px; height: 30px;
    border-radius: 50%;
    background: var(--gold);
    display: flex;
    align-items: center;
    justify-content: center;
  }
  .icon svg { width: 16px; height: 16px; }
  .contact-list {
    position: absolute;
    top: 474px;
    left: 0; right: 0;
    list-style: none;
    text-align: center;
    color: var(--white);
    font-family: Arial, Helvetica, sans-serif;
    font-size: 15.5px;
    line-height: 24px;
  }

  /* Landscape card (brand side) */
  .card-brand {
    width: 700px;
    height: 400px;
    display: flex;
    flex-direction: column;
    align-items: center;
  }
  .card-brand .brand {
    margin-top: 160px;
    font-size: 46px;
    gap: 18px;
  }
  .card-brand .brand-mark { width: 20px; height: 20px; }
  .tagline {
    position: absolute;
    bottom: 52px;
    left: 0; right: 0;
    text-align: center;
    color: var(--gold);
    font-family: Arial, Helvetica, sans-serif;
    font-size: 20px;
    letter-spacing: 0.01em;
  }
</style>
</head>
<body>

  <section class="card card-contact" aria-label="Business card, contact side">
    <div class="brand"><span class="brand-mark"></span>The Loom Briefing</div>

    <div class="name-band">
      <h1 class="person-name">Belinda Harwick</h1>
      <p class="person-title">Director and Stylist</p>
    </div>

    <div class="icon-row">
      <span class="rule"></span>
      <span class="icon" aria-label="Telephone">
        <svg viewBox="0 0 24 24" fill="none" stroke="#1e1e1e" stroke-width="2.2" stroke-linecap="round" stroke-linejoin="round">
          <path d="M5 3h4l2 5-2.5 1.5a11 11 0 0 0 6 6L16 13l5 2v4a2 2 0 0 1-2 2A17 17 0 0 1 3 5a2 2 0 0 1 2-2z"/>
        </svg>
      </span>
      <span class="icon" aria-label="Email">
        <svg viewBox="0 0 24 24" fill="none" stroke="#1e1e1e" stroke-width="2.2" stroke-linejoin="round">
          <rect x="3" y="6" width="18" height="12" rx="1"/>
          <path d="M3 6l9 7 9-7"/>
        </svg>
      </span>
      <span class="icon" aria-label="Website">
        <svg viewBox="0 0 24 24" fill="none" stroke="#1e1e1e" stroke-width="2">
          <circle cx="12" cy="12" r="9"/>
          <ellipse cx="12" cy="12" rx="4" ry="9"/>
          <path d="M3 12h18"/>
        </svg>
      </span>
      <span class="rule"></span>
    </div>

    <ul class="contact-list">
      <li>+61 8 7142 5809</li>
      <li>belinda@theloombriefing.example</li>
      <li>www.theloombriefing.example</li>
    </ul>
  </section>

  <section class="card card-brand" aria-label="Business card, brand side">
    <div class="brand"><span class="brand-mark"></span>The Loom Briefing</div>
    <p class="tagline">Corporate Workwear &amp; Uniform Specialist | Personal Stylist</p>
  </section>

</body>
</html>
```